2-Page Flyer for the Information Session about the Quiet Pathfinder Course

This is a flyer to announce/advertise an evening Information Session about the Quiet Pathfinder Course. This Program aims at mindfully rethinking and redesigning work (and life) for people who feel stuck or not entirely satisfied with their work and/or life (please see draft flyer attached for more details). This Program is property of Bright Meadow, a company that uses a combination of Mindfulness, Design, and Entrepreneurship to help people achieve greater happiness (in their work and lives).

Target Market(s)

People who feel stuck or not entirely satisfied with their work and/or life (please see draft flyer attached for more details)

Font styles to use
Serif
Sans Serif

Colors
ffffff
f37122
33a6d7
acd037

Requirements
Must have
• All of what I will say below is suggestive (I’m not a design expert), and I’m open to divert from it, if it makes sense and feels more interesting.
• I thought initially of a 2-page flyer (please see draft flyer attached). The first page could help people grasp the essence of the event quickly (in 1 or 2 minutes), and then, if they are interested/motivated, they would continue reading through page 2, which has more info about the Program in itself.
• Potential Structure
• Page 1
• . About the Information Session on the Quiet Pathfinder Course
• . Visible Date & Time, Contacts, Venue (and other relevant info)
• . About me (the facilitator)
• Page 2
• . About the Quiet Pathfinder Course
• I include a Powerpoint draft of the flyer with the content. The design is rudimentary and precarious from an aesthetics/organization point of view, and this is mainly where I need help (and maybe in other aspects too!).
• On the flyer, I would like to include:
• . A photo of myself (I attach 1 picture).
• . 1 or 2 beautiful-nature photos (cropped or full). One may have to do with looking at the sky, dreaming, and imagining a new work and life (2 photos with sky and clouds attached). The other has to do with walking the transformation journey (the photo with the person walking through the forest path).
• . bright meadow logo or logos (there are two slightly different ones, that can be used for different purposes). For the first page, I would like the bright meadow logo that has "bright meadow" written on the bottom, with the saying "Stillness, Craft and Venture for Bright Meadow" beneath. This is the main logo. For the 2nd page, you can choose the logo that adapts better.
• - Where it says the "the way out is in" it would be great to have a similar font to the one I attach (see file "Font_the_way_out_is_in.png" and Ankecallig-fg.ttf
Nice to have
• In terms of colours, I would not divert much from the logo colours (and of course white and black). I would like the flyer to be quite white. Almost like fairy-tale white: the white horse, the white snow, the white of the stars, the white heaven. White could be the base colour. White means peace, tranquillity, calm contentment, a smile.
• And then use the other colours. The green of the mindfulness. The blue of the sky, the dreams. And the orange of the sun, the energy, the fire, the action. And maybe the black for text.
• Where it says the "the way out is in" it would be great to have a similar font to the one I attach (see file "Font_the_way_out_is_in".
• I would like this flyer to be a piece of art, in every possible way. Simple, beautiful, ease, light, peaceful, calm happy. Just like the Quiet Pathfinder Course and bright meadow Company that I am creating intends to be. The mission of this Program and Company is to be a designer, a painter (a Picasso) of happier and more fulfilling human lives.
• I am very much looking forward to seeing your proposal(s).

```html
<!DOCTYPE html>
<html lang="en">
<head>
<meta charset="utf-8">
<title>Quiet Pathfinder Course – Information Session Flyer</title>
<link href="https://fonts.googleapis.com/css2?family=Roboto:ital,wght@0,400;0,500;0,700;0,900;1,400&family=Pinyon+Script&display=swap" rel="stylesheet">
<style>
:root{
  --white:#ffffff;
  --orange:#f37122;
  --footer-orange:#ec8633;
  --blue:#33a6d7;
  --bio-blue:#45a7de;
  --green:#acd037;
  --grey:#a7a7a7;
  --ink:#1c1c1c;
  --canvas:#f7f7f9;
}
*{box-sizing:border-box;margin:0;padding:0}
html,body{width:1200px;height:1200px;overflow:hidden;background:var(--canvas)}
body{font-family:"Roboto",Arial,sans-serif;color:var(--ink);position:relative}
.page{position:absolute;top:260px;width:476px;height:672px;background:var(--white);overflow:hidden;box-shadow:0 24px 40px rgba(0,0,0,.28)}
.page--front{left:94px}
.page--back{left:645px}
.abs{position:absolute}
.brand{display:flex;align-items:center;gap:10px}
.brand__dot{width:34px;height:34px;border-radius:50%;background:var(--orange);flex:none}
.brand__name{font-family:"Roboto",Arial,sans-serif;font-weight:400;color:var(--blue);font-size:24px;line-height:.95}
.accent{color:var(--blue)}
/* front */
.hero{left:0;top:0;width:476px;height:360px}
.hero-rule{left:0;top:360px;width:476px;height:6px;background:var(--footer-orange)}
.portrait{left:24px;top:150px;width:179px;height:233px;background:linear-gradient(160deg,#d8d8d8,#8d8d8d 55%,#3c3c3c)}
.bio{left:24px;top:383px;width:179px;height:222px;background:var(--bio-blue);color:var(--ink);padding:10px 10px 0;text-align:center;font-size:7px;line-height:1.3}
.bio::before{content:"";position:absolute;top:-6px;left:84px;border:6px solid transparent;border-top:none;border-bottom-color:var(--bio-blue)}
.bio__label{font-size:7.5px}
.bio__name{font-weight:700;font-size:9px;margin-top:2px}
.bio__role{font-style:italic;font-size:7px;margin-bottom:7px}
.bio__text{text-align:justify;font-size:6.9px;line-height:1.32}
.bio__more{margin-top:7px;font-size:7px}
.bio__more i{display:block}
.title{left:218px;top:184px;width:234px;text-align:center;color:var(--white)}
.title__lead{font-weight:700;font-size:18px;letter-spacing:-.2px}
.title__big{font-weight:900;color:var(--orange);font-size:44px;line-height:1;letter-spacing:.5px;margin-top:2px}
.title__box{border:1.5px solid var(--white);font-weight:500;font-size:12px;letter-spacing:4.6px;padding:2px 0 1px;margin:3px 4px 0}
.title__date{font-weight:700;font-size:15.5px;margin-top:13px;line-height:1.2}
.info{left:224px;top:382px;width:222px;font-size:8px;line-height:1.42}
.info h2{font-size:12px;font-weight:500;text-align:right;margin-bottom:5px}
.info p{text-align:justify}
.info section{margin-bottom:17px}
.contact{text-align:right}
.contact__line{font-size:8.4px;margin-top:4px;display:flex;justify-content:flex-end;gap:6px;align-items:center;white-space:nowrap}
.contact__line span{white-space:nowrap}
.contact__line svg{vertical-align:-1px;margin-right:2px}
.contact__note{font-style:italic;font-size:6px;text-align:right;margin-right:3px}
.venue-bar{left:0;top:632px;width:476px;height:40px;background:var(--footer-orange);color:var(--white);font-weight:700;font-size:14px;display:flex;align-items:center;justify-content:center;gap:6px}
.venue-bar::before{content:"";position:absolute;top:0;left:232px;border:6px solid transparent;border-top-color:var(--white)}
/* back */
.forest{left:0;top:0;width:476px;height:225px;background:linear-gradient(180deg,#2d2418 0%,#4a3a24 35%,#6f6a3a 65%,rgba(255,255,255,0) 100%)}
.back-text{left:24px;width:424px;font-size:7.2px;line-height:1.33;text-align:justify}
.back-text h2{font-size:12px;font-weight:500;margin-bottom:4px;text-align:left}
.back-text h2.blue{color:var(--blue)}
.program-text{width:238px}
.cycle{left:272px;top:266px;width:194px;height:130px}
.quote{left:0;top:593px;width:476px;text-align:center;font-family:"Pinyon Script",cursive;font-size:24px}
.back-footer{left:0;top:633px;width:476px;height:39px;background:var(--footer-orange);color:var(--white);font-size:9px;line-height:1.5;display:flex;align-items:center}
.back-footer__col{flex:1;padding:0 10px;white-space:nowrap}
.back-footer__col--left{text-align:right;border-right:1px solid var(--white)}
.back-footer b{font-weight:700}
.back-footer i{opacity:.9}
</style>
</head>
<body>

<article class="page page--front">
  <svg class="abs hero" viewBox="0 0 476 360" width="476" height="360">
    <defs>
      <linearGradient id="skyToHills" x1="0" y1="0" x2="0" y2="1">
        <stop offset="0" stop-color="#4c8fd1"/>
        <stop offset=".35" stop-color="#b7d2ec"/>
        <stop offset=".55" stop-color="#8aa7c4"/>
        <stop offset=".7" stop-color="#5c7e53"/>
        <stop offset="1" stop-color="#3f7a2e"/>
      </linearGradient>
    </defs>
    <rect role="img" aria-label="Photo: wide blue sky with white clouds over green mountain ridges" width="476" height="360" fill="url(#skyToHills)"/>
    <polygon points="0,0 255,0 215,85 0,85" fill="var(--white)"/>
  </svg>
  <div class="abs brand" style="left:24px;top:12px">
    <span class="brand__dot"></span>
    <span class="brand__name">bright<br>meadow</span>
  </div>

  <div class="abs hero-rule"></div>
  <div class="abs portrait" role="img" aria-label="Black and white portrait photo of the facilitator"></div>

  <div class="abs title">
    <div class="title__lead">Quiet Pathfinder</div>
    <div class="title__big">COURSE</div>
    <div class="title__box">INFORMATION SESSION</div>
    <div class="title__date">THURSDAY 18TH JULY 2019<br>19:30 TO 21:00</div>
  </div>

  <div class="abs bio">
    <div class="bio__label">Facilitator:</div>
    <div class="bio__name">DR TOMAS REYNA</div>
    <div class="bio__role">Visiting Research Fellow, University of Northvale</div>
    <p class="bio__text">Tomas joined the University of Northvale (School of Management) as a Lecturer in Entrepreneurship in 2015. He completed his PhD in Entrepreneurship at Eastbridge Business School (University of Eastbridge) in 2014. His dissertation received the Alder Doctoral Dissertation Award from the Society of Management Studies. Tomas began his working career in the semiconductor industry as a production engineer (Corvale), and then in healthcare as a sales engineer (Halden). After his MBA, he worked as a strategy consultant at Lisden Business School. Originally from Portugal, Tomas enjoys designing and launching new ideas, international communities, mindfulness retreats, and musical improvisation.</p>
    <div class="bio__more">More about the facilitator:<i>www.brightmeadow.example/tomas</i></div>
  </div>

  <div class="abs info">
    <section>
      <h2>Information <span class="accent">Session:</span></h2>
      <p>The purpose of this <b>Information Session</b> is to give you a real insight into the <b>Quiet Pathfinder Course</b> and how it can help you get the most out of your work and life.</p>
    </section>
    <section>
      <h2>How much and <span class="accent">who can come?:</span></h2>
      <p>The Information Session is free and whether you come on your own, or with friends or family, you'll be warmly welcome. It will take place on Thursday the <b>23rd July 2019, from 19:30 to 21:00, at Lantern Coworking</b>. Please get in touch for more info or to book a place.</p>
    </section>
    <section class="contact">
      <h2>Information <span class="accent">&amp; Booking:</span></h2>
      <div style="font-weight:500">Please contact for more information or to book a place</div>
      <div class="contact__line">
        <span><svg width="8" height="7" viewBox="0 0 8 7"><rect x=".5" y=".5" width="7" height="6" fill="none" stroke="var(--orange)"/><path d="M.5 .5 4 4 7.5 .5" fill="none" stroke="var(--orange)"/></svg>hello@brightmeadow.example</span>
        <span><svg width="8" height="8" viewBox="0 0 8 8"><path d="M1 1.5 2.5.5 4 2.5 3 3.5Q4 5 5 5.5L6 4.5 7.8 6 6.8 7.5Q3 7 .8 2Z" fill="var(--orange)"/></svg>+34 600 555 014</span>
      </div>
      <div class="contact__note">(video call and messaging)</div>
    </section>
  </div>

  <div class="abs venue-bar">
    <svg width="10" height="13" viewBox="0 0 10 13"><path d="M5 .8A3.7 3.7 0 0 0 1.3 4.5C1.3 7.3 5 11 5 11S8.7 7.3 8.7 4.5A3.7 3.7 0 0 0 5 .8Z" fill="none" stroke="var(--white)" stroke-width="1.4"/><circle cx="5" cy="4.5" r="1.3" fill="var(--white)"/><path d="M1 12.3H9" stroke="var(--white)" stroke-width="1.2"/></svg>
    Venue: Lantern Coworking, C/ Almendro 42, Barcelona
  </div>
</article>

<article class="page page--back">
  <div class="abs forest" role="img" aria-label="Photo: a person walking down a long path through a dark pine forest"></div>
  <svg class="abs" style="left:0;top:0" width="476" height="70" viewBox="0 0 476 70"><polygon points="275,0 476,0 476,68 305,68" fill="var(--white)"/></svg>
  <div class="abs brand" style="left:314px;top:14px">
    <span class="brand__dot"></span>
    <span class="brand__name">bright<br>meadow</span>
  </div>

  <div class="abs back-text" style="top:215px">
    <h2>What is <span class="accent">Quiet Pathfinder Course</span></h2>
    <p>Being mindful means being aware and awake. Entrepreneurship is the creation of a new form of organising. The <b>Quiet Pathfinder Course</b> is then the process of creating or redesigning your work and life with awareness, in a way that is reflective of you, of your passions and values, thus conducing to a greater sense of fulfilment and happiness.</p>
  </div>

  <div class="abs back-text program-text" style="top:278px">
    <h2>The <span class="accent">Program</span></h2>
    <p>The <b>Quiet Pathfinder Course</b> is a <b>4-month long transformative journey</b> for people who feel stuck or not entirely satisfied with their work and/or life. It will be of benefit for everyone, at any stage. The Program consists of a series of four 5-hour workshops, one per month, complemented by 2-hour weekly peer support meetings. It combines mindfulness techniques, design thinking methodology and entrepreneurship frameworks to achieve the desired outcomes.</p>
  </div>

  <svg class="abs cycle" viewBox="0 0 194 130" role="img" aria-label="Cycle of four workshops joined by weekly peer support meetings">
    <defs>
      <marker id="tip" markerWidth="6" markerHeight="6" refX="3" refY="3" orient="auto"><path d="M0 0 6 3 0 6Z" fill="context-stroke"/></marker>
    </defs>
    <circle cx="90" cy="65" r="38" fill="#ededed"/>
    <path d="M58 36 L58 26 L70 26" fill="none" stroke="#555" stroke-width="2.5" marker-end="url(#tip)"/>
    <path d="M112 26 L124 26 L124 36" fill="none" stroke="var(--green)" stroke-width="2.5" marker-end="url(#tip)"/>
    <path d="M124 92 L124 102 L112 102" fill="none" stroke="var(--blue)" stroke-width="2.5" marker-end="url(#tip)"/>
    <path d="M70 104 L58 104 L58 94" fill="none" stroke="var(--orange)" stroke-width="2.5" marker-end="url(#tip)"/>
    <g font-family="Roboto,Arial,sans-serif" font-size="4.6" fill="var(--white)" text-anchor="middle">
      <circle cx="90" cy="22" r="21" fill="var(--green)"/>
      <text x="90" y="18">Workshop 1</text><text x="90" y="24">-INSIGHT-</text><text x="90" y="30" font-style="italic">(5 hours)</text>
      <circle cx="133" cy="63" r="21" fill="var(--blue)"/>
      <text x="133" y="59">Workshop 2</text><text x="133" y="65">-DESIGN-</text><text x="133" y="71" font-style="italic">(3 hours)</text>
      <circle cx="90" cy="104" r="21" fill="var(--footer-orange)"/>
      <text x="90" y="100">Workshop 3</text><text x="90" y="106">-EXECUTE-</text><text x="90" y="112" font-style="italic">(5 hours)</text>
      <circle cx="47" cy="63" r="21" fill="var(--grey)"/>
      <text x="47" y="59">Workshop 4</text><text x="47" y="65">-PRESENT-</text><text x="47" y="71" font-style="italic">(5 hours)</text>
    </g>
    <g font-family="Roboto,Arial,sans-serif" font-size="4.6" fill="var(--ink)">
      <text x="14" y="19">WPS Meetings</text>
      <text x="192" y="13" text-anchor="end">Weekly Peer Support</text>
      <text x="189" y="19" text-anchor="end">(WPS) meetings</text>
      <text x="14" y="115">WPS Meetings</text>
      <text x="192" y="115" text-anchor="end">WPS Meetings</text>
    </g>
  </svg>

  <div class="abs back-text" style="top:404px">
    <h2 class="blue">Why</h2>
    <p>Many people are not entirely satisfied with their work, but they don't know what to do about it. The Quiet Pathfinder Course offers an opportunity, a safe place, a collective journey to help you reflect, design, and (very likely) do something about it.</p>
    <p style="text-align:left">By the end of the Program, you should have:<br>1) Increased awareness, clarity and confidence<br>2) A deeper insight on what makes you happier and what you want<br>3) A clear design integrating your intended work and life<br>4) Initiated the execution of this design.</p>
  </div>

  <div class="abs back-text" style="top:500px">
    <h2 class="blue">How</h2>
    <p style="text-align:left">This Program differs from existing entrepreneurial programs in many ways:<br>1) It starts upstream with mindfulness and self analysis to look deeply into yourself<br>2) Design and execution decisions are rooted on happiness rather than (only) financials</p>
    <p>3) The process is holistic and inclusive, aiming at designing an integrated work and life, and on building synergies between your different parts.</p>
    <p>The Program format includes lectures, individual work, group sharing, guided activities, experiential exercises, video, audio, handouts and other resources.</p>
  </div>

  <div class="abs quote">“The Way Out is In”</div>

  <div class="abs back-footer">
    <div class="back-footer__col back-footer__col--left">
      <div><b>Date:</b> Thursday 23th, from 19:30 to 21:00</div>
      <div><b>Venue:</b> Lantern Coworking, C/ Almendro 42, Barcelona</div>
    </div>
    <div class="back-footer__col">
      <div><b>Email:</b> hello@brightmeadow.example</div>
      <div><b>Tel:</b> +34 600 555 014 <i>(video call and messaging)</i></div>
    </div>
  </div>
</article>

</body>
</html>
```